Website for a company offering full serivce charging solutions for electric cars

The company "tanu-werk" (english: "tanu-works") offering all-in-one-solutions for charging infrastructure for electric mobility.

There are four products:
1- Wallboxes for single-family homes
2- Solutions for property devloper/-management for property parking space
3- All-in-one-charging solution for municipalities/communities
4- Solutions for tourism/hotels/holiday appartments

The Website structure:
1. Main Page
2.1. Product Page Single Homes
2.2. Product Page Property Management / Parking
2.3. Product Page Municipality
2.4. Product Page Tourism
3. Contact Form / Request for information
4. Imprint / Legal

The Website should be built on Wordpress with a powerful possibility to simply add/modify specific landing pages.

We would like you to implement the website later and also maintain it if possible, but we would be able to do minor modifications by ourselfs (for A/B-Testing)

The website should be clear and simple, easy to understand.
Target group is mainly B2C without deeper knowledge of that topic.

It should suggest, that we will provide a very simple way to get the charging infrastructure done.

We need a contact form, maybe we will use Hubspot later.

Attached you will find a draft of the main page and a landing page (for 2.2) - it is just the content, please ignore the design. We would love to let you create a suitable design.
Also you will find some drafts a bit different for the same story.

I added also a few stock photos, but they don't need to be used! If you have better ideas, you are welcome!

Industry/Entity Type

Charging/Electric mobility

Number of Pages Required

2 page

Font styles to use
Sans Serif

Requirements
Must have
• Based on Wordpress, and the designer should be able to implement it on Wordpress on a later step

```html
<!DOCTYPE html>
<html lang="de">
<head>
<meta charset="utf-8">
<title>tanu-werk – Ladelösungen für E-Mobilität</title>
<link href="https://fonts.googleapis.com/css2?family=Mulish:wght@400;600;700;800&family=Saira+Semi+Condensed:wght@400;500;600&display=swap" rel="stylesheet">
<style>
:root{
  --bg:#161b2e;
  --bg-deep:#11152a;
  --magenta:#e21fa6;
  --pink:#ff3cc0;
  --purple:#7a3ed2;
  --violet:#9b4be0;
  --text:#ffffff;
  --muted:#b9bccb;
  --line:#3a3f57;
}
*{box-sizing:border-box;margin:0;padding:0}
html,body{width:1200px;height:4293px;overflow:hidden}
body{background:var(--bg);color:var(--text);font-family:"Mulish",sans-serif;position:relative}
.abs{position:absolute}

/* header */
.site-header{position:absolute;left:0;top:0;width:1200px;height:83px;background:var(--bg);z-index:5}
.brand{position:absolute;left:92px;top:18px;display:flex;align-items:center;gap:12px}
.brand-dot{width:34px;height:34px;border-radius:50%;background:var(--magenta)}
.brand-name{font-size:24px;font-weight:700;line-height:1}
.brand-tag{font-size:13px;font-weight:600;margin-top:3px}
.main-nav a{position:absolute;top:28px;font-size:14px;color:var(--muted);text-decoration:none;letter-spacing:.3px}
.main-nav a.active{color:#fff}
.main-nav a.active::after{content:"";position:absolute;left:0;right:0;bottom:-11px;height:3px;background:var(--magenta)}
.lang{position:absolute;left:1035px;top:20px;width:78px;height:34px;border:1px solid #555a72;font-size:13px;display:flex;align-items:center;justify-content:center;gap:4px}

/* hero */
.hero{position:absolute;left:0;top:83px;width:1200px;height:660px}
.hero-bg{position:absolute;inset:0;background:radial-gradient(ellipse at 75% 30%,#3b3358 0%,#2a2943 40%,#1a1d31 80%);clip-path:polygon(0 0,100% 0,100% 552px,600px 655px,0 552px)}
.hero-edge{position:absolute;left:0;top:0}
.hero h1{position:absolute;left:113px;top:155px;font-family:"Mulish",sans-serif;font-size:46px;line-height:54px;font-weight:400;text-transform:uppercase}
.hero h1 strong{font-weight:800}
.hero-lead{position:absolute;left:120px;top:270px;font-size:19px;line-height:30px;width:440px}
.btn-primary{position:absolute;left:117px;top:359px;width:191px;height:50px;border-radius:25px;background:linear-gradient(90deg,var(--purple),var(--magenta));font-size:15px;font-weight:800;display:flex;align-items:center;justify-content:center;letter-spacing:.5px}
.hero-photo{position:absolute;left:628px;top:104px;width:360px;height:360px;border-radius:50%;background:radial-gradient(circle at 45% 40%,#6fb6ff 0%,#2e5fd0 25%,#c9d3e6 45%,#7785a8 70%,#3d4468 100%)}
.dot-line{position:absolute;height:0;border-top:2px dotted #9a9fb5}

/* intro */
.intro-mark{position:absolute;left:578px;top:808px;width:44px;height:34px;border:3px solid var(--magenta);border-radius:50%}
.intro-title{position:absolute;left:150px;top:856px;width:900px;text-align:center;font-size:21px;line-height:33px;font-weight:800}
.intro-text{position:absolute;left:180px;top:962px;width:840px;text-align:center;font-size:15.5px;line-height:27px;color:var(--muted)}
.glow-band{position:absolute;left:0;width:1200px;background:linear-gradient(180deg,rgba(22,27,46,0) 0%,rgba(120,50,170,.35) 55%,rgba(22,27,46,0) 100%)}

.ask-title{position:absolute;left:200px;top:1250px;width:800px;text-align:center;font-family:"Saira Semi Condensed",sans-serif;font-size:31px;line-height:44px;font-weight:400}
.ask-title strong{font-weight:600}

/* choice cards */
.choice{position:absolute;top:1383px;width:325px;height:179px;background:linear-gradient(135deg,#3c4458,#1f2436);display:flex;flex-direction:column;align-items:center;justify-content:center;font-family:"Saira Semi Condensed",sans-serif;font-size:25px}
.choice strong{font-weight:600}
.choice.active{top:1375px;height:195px;background:linear-gradient(120deg,#5d3dc6 0%,#9a2fc0 50%,var(--magenta) 100%);box-shadow:0 10px 30px rgba(226,31,166,.35)}
.choice .chev{margin-top:20px}
.dots{position:absolute;background-image:radial-gradient(#5a5f78 1.2px,transparent 1.4px);background-size:10px 10px}

/* offer sections */
.offer-photo{position:absolute;border-radius:50%}
.offer-title{position:absolute;font-family:"Saira Semi Condensed",sans-serif;font-size:40px;font-weight:400;line-height:48px}
.offer-title span{color:var(--magenta);font-weight:500}
.offer-list{position:absolute;list-style:none;font-size:13px;line-height:17px;color:#e3e4ec}
.offer-list li{margin-bottom:7px}
.offer-list.chev li{padding-left:16px;position:relative}
.offer-list.chev li::before{content:"";position:absolute;left:0;top:4px;width:6px;height:6px;border-right:2px solid var(--magenta);border-top:2px solid var(--magenta);transform:rotate(45deg)}
.offer-list ul{list-style:none;margin:6px 0 10px 0}
.offer-list ul li{margin-bottom:2px}

/* contact */
.contact{position:absolute;left:0;top:3517px;width:1200px;height:575px;background:linear-gradient(100deg,#6b2fb8 0%,#8a2fb8 45%,#c0209f 100%)}
.contact-photo{position:absolute;left:0;top:0;width:1200px;height:575px;clip-path:polygon(750px 0,1200px 0,1200px 575px,617px 575px);background:radial-gradient(ellipse at 70% 60%,#4fe3e0 0%,#1c8fa3 20%,#2d3350 50%,#1a1b2c 100%)}
.contact h2{position:absolute;left:137px;top:76px;font-family:"Mulish",sans-serif;font-size:38px;font-weight:400;letter-spacing:1px}
.contact h2 strong{font-weight:800}
.field{position:absolute;left:143px;width:412px;height:46px;background:#fff;color:#666;font-size:12px;display:flex;align-items:center;gap:8px;padding-left:16px}
.field.message{height:96px;align-items:flex-start;padding-top:16px}
.btn-outline{position:absolute;left:145px;top:431px;width:180px;height:49px;border:2px solid #fff;display:flex;align-items:center;justify-content:center;font-weight:800;font-size:15px}

/* footer */
.footer-nav{position:absolute;left:0;top:4143px;width:1200px;display:flex;justify-content:center;gap:47px;font-size:13px;font-weight:800}
.copyright{position:absolute;left:0;top:4172px;width:1200px;text-align:center;font-size:13px;color:var(--muted)}
.social{position:absolute;top:4207px;width:40px;height:40px;border-radius:50%;border:2px solid var(--magenta)}
</style>
</head>
<body>

<header class="site-header">
  <div class="brand">
    <span class="brand-dot"></span>
    <div><div class="brand-name">tanu-werk.de</div><div class="brand-tag">einfach mehr als laden</div></div>
  </div>
  <nav class="main-nav">
    <a class="active" style="left:407px">LÖSUNGEN</a>
    <a style="left:533px">UNTERNEHMEN</a>
    <a style="left:693px">SERVICES</a>
    <a style="left:812px">KARRIERE</a>
    <a style="left:928px">KONTAKT</a>
  </nav>
  <div class="lang">ENG <svg width="10" height="8" viewBox="0 0 10 8"><path d="M1 2l4 4 4-4" stroke="#fff" stroke-width="1.6" fill="none"/></svg></div>
</header>

<section class="hero">
  <div class="hero-bg" role="img" aria-label="Elektroauto an einer Ladesäule im Hintergrund"></div>
  <svg class="hero-edge" width="1200" height="660" viewBox="0 0 1200 660">
    <defs><linearGradient id="edge" x1="0" x2="1"><stop offset="0" stop-color="#7a3ed2"/><stop offset="1" stop-color="#e21fa6"/></linearGradient>
    <linearGradient id="ring" x1="0" y1="1" x2="1" y2="0"><stop offset="0" stop-color="#7a3ed2"/><stop offset="1" stop-color="#e21fa6"/></linearGradient></defs>
    <path d="M0 552 L600 655 L1200 552" stroke="url(#edge)" stroke-width="6" fill="none"/>
    <path d="M808 71 A213 213 0 1 1 595 284" stroke="url(#ring)" stroke-width="8" fill="none" stroke-linecap="round"/>
    <circle cx="478" cy="178" r="4" fill="#fff"/>
  </svg>
  <div class="hero-photo" role="img" aria-label="Nahaufnahme eines Ladesteckers mit blau leuchtendem Ring"></div>
  <div class="dot-line" style="left:482px;top:178px;width:150px"></div>
  <h1><strong>tanu-werk ist</strong><br>Ihr Partner</h1>
  <p class="hero-lead">wenn das Laden nicht nur einfach, sondern die Umsetzung auch aus einer Hand kommen soll</p>
  <div class="btn-primary">LEARN MORE</div>
</section>

<div class="intro-mark" aria-hidden="true"></div>
<p class="intro-title">Wir&nbsp; bieten Lösungen sowohl für Privatkunden, Geschäftskunden als auch Kommunen an, die schnell, fair und ohne Eigenleistung zu einer smarten Ladelösung für E-Fahrzeuge kommen möchten.</p>
<p class="intro-text">Von der Beratung, über die Installation, Inbetriebnahme bis zur Abrechnung und Wartung bekommen Sie bei tanu-werk alles aus einer Hand. Auf Wunsch vermieten wir auch die Ladetechnik und übernehmen im gewerblichen Bereich die direkte Abrechnung mit dem Nutzer. Für Kommunen bieten wir den kostenfreien Full-Service an und beteiligen die Gemeinden an der Nutzung der Infrastruktur.</p>

<div class="glow-band" style="top:1083px;height:135px"></div>
<svg class="abs" style="left:610px;top:1192px" width="28" height="42" viewBox="0 0 28 42"><path d="M17 2 L4 24 H14 L10 40 L24 17 H14 Z" stroke="#e21fa6" stroke-width="2.5" fill="none" stroke-linejoin="round"/></svg>
<h2 class="ask-title"><strong>Fragen Sie uns nach der auf Ihre individuellen</strong><br>Bedürfnisse zugeschnittenen Lösung:</h2>

<div class="dots" style="left:95px;top:1445px;width:210px;height:140px"></div>
<div class="dots" style="left:945px;top:1355px;width:210px;height:90px"></div>
<div class="choice" style="left:120px" role="img" aria-label="Hintergrundbild: Auto vor einer Ladestation">
  <span>Als <strong>Privatkunde</strong></span>
  <svg class="chev" width="14" height="14" viewBox="0 0 14 14"><path d="M2 2l5 5 5-5M2 7l5 5 5-5" stroke="#fff" stroke-width="1.8" fill="none"/></svg>
</div>
<div class="choice active" style="left:467px">
  <span>als <strong>Geschäftskunde</strong></span>
  <svg class="chev" width="14" height="14" viewBox="0 0 14 14"><path d="M2 2l5 5 5-5M2 7l5 5 5-5" stroke="#fff" stroke-width="1.8" fill="none"/></svg>
</div>
<div class="choice" style="left:810px" role="img" aria-label="Hintergrundbild: öffentliche Ladesäule bei Nacht">
  <span>Als <strong>Kommune</strong></span>
  <svg class="chev" width="14" height="14" viewBox="0 0 14 14"><path d="M2 2l5 5 5-5M2 7l5 5 5-5" stroke="#fff" stroke-width="1.8" fill="none"/></svg>
</div>

<!-- rings and connectors -->
<svg class="abs" style="left:0;top:1600px" width="1200" height="1830" viewBox="0 1600 1200 1830">
  <defs>
    <linearGradient id="r1" x1="0" y1="0" x2="1" y2="1"><stop offset="0" stop-color="#e21fa6"/><stop offset="1" stop-color="#7a3ed2"/></linearGradient>
    <linearGradient id="r2" x1="1" y1="0" x2="0" y2="1"><stop offset="0" stop-color="#e21fa6"/><stop offset="1" stop-color="#7a3ed2"/></linearGradient>
  </defs>
  <circle cx="322" cy="1888" r="228" fill="#1c2036"/>
  <path d="M445 1690 A233 233 0 0 0 96 1940" stroke="url(#r1)" stroke-width="8" fill="none" stroke-linecap="round"/>
  <path d="M552 1920 A233 233 0 0 1 250 2110" stroke="url(#r2)" stroke-width="8" fill="none" stroke-linecap="round"/>
  <path d="M430 2120 V2180 Q430 2208 458 2208 H822 Q850 2208 850 2236 V2290" stroke="#a0249e" stroke-width="3" fill="none"/>
  <circle cx="900" cy="2513" r="232" fill="#1c2036"/>
  <path d="M680 2480 A230 230 0 0 1 1020 2310" stroke="url(#r1)" stroke-width="8" fill="none" stroke-linecap="round"/>
  <path d="M1125 2530 A230 230 0 0 1 790 2710" stroke="url(#r2)" stroke-width="8" fill="none" stroke-linecap="round"/>
  <path d="M847 2745 V2800 Q847 2820 819 2820 H453 Q425 2820 425 2848 V2885" stroke="#a0249e" stroke-width="3" fill="none"/>
  <circle cx="350" cy="3142" r="228" fill="#1c2036"/>
  <path d="M135 3080 A228 228 0 0 1 450 2935" stroke="url(#r1)" stroke-width="8" fill="none" stroke-linecap="round"/>
  <path d="M565 3200 A228 228 0 0 1 230 3335" stroke="url(#r2)" stroke-width="8" fill="none" stroke-linecap="round"/>
  <circle cx="646" cy="1735" r="3.5" fill="#fff"/><path d="M652 1735 H760" stroke="#9a9fb5" stroke-width="2" stroke-dasharray="2 3"/>
  <circle cx="141" cy="2306" r="3.5" fill="#fff"/><path d="M147 2306 H255" stroke="#9a9fb5" stroke-width="2" stroke-dasharray="2 3"/>
</svg>

<div class="offer-photo" style="left:130px;top:1696px;width:384px;height:384px;background:radial-gradient(circle at 45% 60%,#e6edf5 0%,#8da6bd 30%,#3d566c 60%,#1d2a3a 100%)" role="img" aria-label="Weißes Elektroauto lädt an einer Wallbox"></div>
<h2 class="offer-title" style="left:638px;top:1684px">als <span>Privatkunde</span></h2>
<ul class="offer-list" style="left:643px;top:1755px;width:500px">
  <li>Bestandsanalyse mit umfangreicher Beratung über die Möglichkeiten der Umsetzung</li>
  <li>Prüfung und Übernahme der Anmeldung verfügbarer Fördermöglichkeiten</li>
  <li>Auswahl an smarten Wallbox Lösungen, passend für Ihr Fahrzeug und Ihre Bedürfnisse</li>
  <li>Installation inkl. aller notwendigen Materialien und Tätigkeiten (Durchbrüche, Erdarbeiten, etc.)</li>
  <li>Inbetriebnahme und Einweisung in die Ladetechnik</li>
  <li>Jährlich technische Wartung nach DGUV3</li>
  <li>Reparaturservice, unter Berücksichtigung der geltenden Garantie Ansprüche</li>
  <li>Installation inkl. aller notwendigen Materialien und Tätigkeiten (Durchbrüche, Erdarbeiten, etc.</li>
  <li>Inbetriebnahme und Einweisung in die Ladetechnik</li>
  <li>Jährlich technische Wartung nach DGUV3</li>
  <li>Reparaturservice, unter Berücksichtigung der geltenden Garantie Ansprüche</li>
</ul>

<h2 class="offer-title" style="left:137px;top:2254px">als <span>Geschäftskunde</span></h2>
<ul class="offer-list chev" style="left:135px;top:2324px;width:510px">
  <li>Durchführung einer individuellen Bedarfsanalyse inkl. Ermittlung der Anforderungen für:
    <ul>
      <li>Haus- und Immobilienverwaltungen</li>
      <li>Dienstleistungs- und Handelsunternehmen</li>
      <li>Hotel und Beherbergungsbetriebe</li>
      <li>Parkraum- und Parkhausbetreiber</li>
      <li>Tourismus, Sport- und Freizeiteinrichtungen</li>
    </ul></li>
  <li>Planung und Projektierung des Installationsaufwands inkl. Materialverbrauch</li>
  <li>Leasing oder Kauf der Hardware</li>
  <li>Normgerechte Installation der Ladeinfrastruktur inkl. Durchbruch-, Brandschutz- und Erdarbeiten</li>
  <li>Bei Bestandsbauten Integration der Ladeinfrastruktur in die Gebäudesystemtechnik und ggf. Anpassung des Netzanschlusses</li>
  <li>Inbetriebnahme der Anlage inkl. Prüf- und Messprotokollen</li>
  <li>Wiederkehrende technische Prüfung der Anlage nach DGUV 3</li>
  <li>Austausch und Reparatur Service</li>
  <li>Unterstützung bei der mtl. Nutzungsabrechnung und Einbindung in Ihre vorhandene Abrechnungssysteme</li>
  <li>ODER direkte Abrechnung mit den Nutzern</li>
</ul>
<div class="offer-photo" style="left:706px;top:2319px;width:390px;height:390px;background:radial-gradient(circle at 40% 55%,#3a63d6 0%,#1f2a5c 35%,#3b4058 60%,#7c8294 100%)" role="img" aria-label="Ladekabel mit blauem Stecker an einer Ladesäule"></div>

<div class="offer-photo" style="left:157px;top:2948px;width:386px;height:386px;background:radial-gradient(circle at 50% 50%,#d9dbd6 0%,#a7ab9f 40%,#5c6052 75%,#2c3028 100%)" role="img" aria-label="Frau mit Einkaufstasche lädt ihr Auto an einer öffentlichen Ladesäule"></div>
<h2 class="offer-title" style="left:625px;top:2889px">als <span>Kommune</span></h2>
<ul class="offer-list chev" style="left:628px;top:2964px;width:520px">
  <li>Konzeptionierung möglicher Ladeinfrastrukturen innerhalb Ihrer Gemeinde</li>
  <li>Planung und Projektsteuerung inkl. sämtlicher behördlicher Genehmigungsverfahren und Beantragung von Fördermitteln</li>
  <li>Fachgerechte Installation und Inbetriebnahme</li>
  <li>Regelmäßige Wartung gemäß Vorschrif</li>
  <li>Reparatur und Kundenservice</li>
  <li>Direkte Abrechnung mit dem Nutzer</li>
  <li>Beteiligung der Gemeinde am Umsatz</li>
  <li>Möglichkeit der Integration von Bonusprogrammen, mit denen der lokale Einzelhandel beworben wird</li>
  <li>von Fördermitteln<br>Fachgerechte Installation und Inbetriebnahme</li>
  <li>Regelmäßige Wartung gemäß Vorschrif</li>
  <li>Reparatur und Kundenservice</li>
  <li>Direkte Abrechnung mit dem Nutzer</li>
  <li>Beteiligung der Gemeinde am Umsatz</li>
  <li>Möglichkeit der Integration von Bonusprogrammen, mit denen der lokale Einzelhandel beworben wird</li>
</ul>

<div class="glow-band" style="top:3400px;height:117px"></div>

<section class="contact">
  <div class="contact-photo" role="img" aria-label="Hand steckt einen Ladestecker mit türkis leuchtenden Lichtspuren ein"></div>
  <h2>CONTACT <strong>US</strong></h2>
  <div class="field" style="top:150px"><svg width="14" height="14" viewBox="0 0 14 14"><circle cx="7" cy="4.5" r="3" stroke="#777" fill="none" stroke-width="1.3"/><path d="M1.5 13c0-3 2.5-4.5 5.5-4.5s5.5 1.5 5.5 4.5" stroke="#777" fill="none" stroke-width="1.3"/></svg>Your Name*</div>
  <div class="field" style="top:205px"><svg width="15" height="12" viewBox="0 0 15 12"><rect x="1" y="1" width="13" height="10" stroke="#777" fill="none" stroke-width="1.3"/><path d="M1 1l6.5 5.5L14 1" stroke="#777" fill="none" stroke-width="1.3"/></svg>Email address*</div>
  <div class="field" style="top:260px"><svg width="14" height="14" viewBox="0 0 14 14"><path d="M3 1l2.5 3-1.5 1.8c.8 1.8 2.4 3.4 4.2 4.2L10 8.5l3 2.5-1.5 2C6 13 1 8 1 2.5Z" fill="#777"/></svg>Phone number*</div>
  <div class="field message" style="top:315px">Leave Message</div>
  <div class="btn-outline">SUBMIT NOW</div>
</section>

<footer>
  <nav class="footer-nav"><span>AGB</span><span>DATENSCHUTZERKLÄRUNG</span><span>IMPRESSUM</span><span>KONTAKT</span><span>KARRIERE</span><span>FAQS</span></nav>
  <p class="copyright">© 2022 tanu-werk GmbH |&nbsp; All Right Reserved</p>
  <span class="social" style="left:530px" aria-label="Social-Media-Link"></span>
  <span class="social" style="left:578px" aria-label="Social-Media-Link"></span>
  <span class="social" style="left:626px" aria-label="Social-Media-Link"></span>
</footer>

</body>
</html>
```